Logo and Card design for KRV Home Solutions LLC

I need an edgier logo and business card designs. Current logo attached. I like the colors below. I would like the logo to incorporate a home in the design.
Title = Principal-Acquisitions
Email:KRVHOMESOLUTIONS@fernmail.example
555-214-0937
facebook
IG
2 sided business card with the front being contact info a slogan about selling a home fast. The back incorporating What we do. Buy houses, land, or commercial property as is. We find solutions to make the process of selling simple and fair.

Target Market(s)

Motivated house sellers.

Industry/Entity Type

Business

Contact Information for Business Card

Who we are: We are a Faith based Real Estate Investment Company. We pay cash for homes in any condition and can close quick. Whatever the reason you need to sell fast, we can help. We believe in creating win-win solutions to help you in your time of need. We care! We can help!

Logo Text

KRV Home Solutions LLC

Font styles to use
Sans Serif

Colors
33a6d7
0355a3
85abd2
cee9f5
9d9d9d
b2b2b2
ffffff

Requirements
Must have
• Old logo attached. I want something edgier.
• Company name, phone number, description on the back of what we can do. Pay all cash. Buy in as is condition. No fees,Commisions or closing costs.Close quick. No hassles with solutions to meet your unique situation.
• Call today for an offer within 24 hours.

```html
<!DOCTYPE html>
<html lang="en">
<head>
<meta charset="utf-8">
<title>KRV Home Solutions – Business Card</title>
<link rel="stylesheet" href="https://fonts.googleapis.com/css2?family=Roboto:wght@400;500;700&family=Roboto+Condensed:wght@400;700&display=swap">
<style>
  :root {
    --backdrop: #2b2b2b;
    --navy: #1f3a6d;
    --navy-deep: #1d376a;
    --slate: #5f6062;
    --band-grey: #666667;
    --text-grey: #5a5a5a;
    --white: #ffffff;
    --photo-light: #e6eef3;
    --photo-mid: #cfdde6;
    --photo-green: #c9d8cf;
  }
  * { box-sizing: border-box; margin: 0; padding: 0; }
  html, body { width: 1200px; height: 960px; overflow: hidden; }
  body { background: var(--backdrop); position: relative; font-family: "Roboto", sans-serif; }

  .card { position: absolute; width: 600px; height: 343px; overflow: hidden; }

  /* Front */
  .card-front { left: 314px; top: 113px; }
  .front-photo {
    position: absolute; inset: 0;
    background: linear-gradient(100deg, var(--photo-light) 0%, var(--photo-mid) 45%, var(--photo-light) 70%, var(--photo-green) 100%);
  }
  .brand-block {
    position: absolute; left: 60px; top: 118px; width: 176px;
    display: flex; align-items: center; gap: 8px;
  }
  .brand-mark { width: 14px; height: 14px; background: var(--navy); flex: none; }
  .brand-name {
    font-family: "Roboto", sans-serif; font-weight: 700; font-size: 19px;
    line-height: 1.15; color: var(--navy); letter-spacing: 0.3px;
  }
  .divider { position: absolute; left: 260px; top: 74px; width: 1px; height: 128px; background: #a9b3bb; }
  .person { position: absolute; left: 285px; top: 80px; }
  .person-name {
    font-family: "Roboto Condensed", sans-serif; font-weight: 700; font-size: 23px;
    color: var(--navy); letter-spacing: 0.2px; line-height: 1;
  }
  .person-title {
    font-family: "Roboto", sans-serif; font-weight: 500; font-size: 15px;
    color: var(--text-grey); margin-top: 6px;
  }
  .contact-list { position: absolute; left: 286px; top: 135px; list-style: none; }
  .contact-list li {
    display: flex; align-items: center; gap: 8px; height: 19px;
    font-size: 14.5px; color: #444; 
  }
  .contact-list svg { width: 13px; height: 13px; fill: var(--navy); flex: none; }
  .offer-band {
    position: absolute; left: 0; top: 247px; width: 100%; height: 77px;
    background: var(--band-grey);
    border-top: 4px solid var(--navy); border-bottom: 4px solid var(--navy);
    display: flex; flex-direction: column; justify-content: center; align-items: center;
    font-family: "Roboto Condensed", sans-serif; font-size: 14.5px; line-height: 17.5px;
    color: var(--white); text-align: center;
  }

  /* Back */
  .card-back { left: 311px; top: 472px; background: var(--navy-deep); color: var(--white); text-align: center; }
  .back-brand {
    position: absolute; left: 0; top: 80px; width: 100%;
    display: flex; justify-content: center; align-items: center; gap: 10px;
  }
  .back-brand .brand-mark { background: var(--white); width: 16px; height: 16px; }
  .back-brand .brand-name { color: var(--white); font-size: 26px; }
  .section-title { position: absolute; left: 0; width: 100%; font-weight: 700; font-size: 15px; }
  .section-body { position: absolute; left: 0; width: 100%; font-size: 14.5px; line-height: 18px; }
  .who-title { top: 169px; }
  .who-body { top: 190px; }
  .what-title { top: 255px; }
  .what-body { top: 276px; }
</style>
</head>
<body>

<section class="card card-front">
  <div class="front-photo" role="img" aria-label="Faded photo of a suburban house with trees and a person in the foreground"></div>

  <div class="brand-block">
    <span class="brand-mark"></span>
    <span class="brand-name">KRV HOME SOLUTIONS</span>
  </div>

  <div class="divider"></div>

  <div class="person">
    <div class="person-name">ALEX MORGAN</div>
    <div class="person-title">Principal-Acquisitions</div>
  </div>

  <ul class="contact-list">
    <li>
      <svg viewBox="0 0 24 24"><path d="M6.6 10.8a15.1 15.1 0 0 0 6.6 6.6l2.2-2.2a1 1 0 0 1 1-.25 11.4 11.4 0 0 0 3.6.57 1 1 0 0 1 1 1V20a1 1 0 0 1-1 1A17 17 0 0 1 3 4a1 1 0 0 1 1-1h3.5a1 1 0 0 1 1 1c0 1.25.2 2.45.57 3.57a1 1 0 0 1-.25 1z"/></svg>
      555-214-0937
    </li>
    <li>
      <svg viewBox="0 0 24 24"><path d="M2 5h20v14H2z" fill="none"/><path d="M2 5h20v14H2V5zm2 2v.5l8 5 8-5V7H4z"/></svg>
      KRVHOMESOLUTIONS@fernmail.example
    </li>
    <li>
      <svg viewBox="0 0 24 24"><circle cx="12" cy="12" r="10"/></svg>
      KRVHOMESOLUTIONS.example
    </li>
  </ul>

  <div class="offer-band">
    <p>Pay all cash. Buy in as is condition.• No fees,Commisions or closing costs.</p>
    <p>Close quick. No hassles with solutions to meet your unique situation.</p>
    <p>Call today for an offer within 24 hours.</p>
  </div>
</section>

<section class="card card-back">
  <div class="back-brand">
    <span class="brand-mark"></span>
    <span class="brand-name">KRV HOME SOLUTIONS</span>
  </div>

  <h2 class="section-title who-title">WHO WE ARE</h2>
  <p class="section-body who-body">We are a Faith based Real Estate Investment Company. We pay cash for<br>homes in any condition and can close quick. Whatever the reason you need<br>to sell fast, we can help. We believe in creating win-win solutions to help</p>

  <h2 class="section-title what-title">WHAT WE DO</h2>
  <p class="section-body what-body">Buy houses, land, or commercial property as is.<br>We find solutions to make the process of selling simple and fair.</p>
</section>

</body>
</html>
```